Business card design

I need my logo on this card, things I need the card to have on it
licensed and insured.
owner operators Milo & Trent Halvorsen
my phone number 5083716254
Disaster Recovery, Storm Damage Restoration, Proactive Disaster Plan Management, Roof Repair/Restoration Structural Repair and Reconstruction, Emergency Boarding and Tarping Service, Perimeter Fencing, Emergency Tree Removal,

```html
<!DOCTYPE html>
<html lang="en">
<head>
<meta charset="utf-8">
<title>Halvorsen's Construction – Business Card</title>
<link href="https://fonts.googleapis.com/css2?family=Raleway:wght@400;500&family=Montserrat:wght@400;500&display=swap" rel="stylesheet">
<style>
  :root {
    --stage: #9b9b9b;
    --card-grey: #737377;
    --card-white: #ffffff;
    --brand-blue: #3d8fd3;
    --text-dark: #222222;
    --text-light: #ffffff;
    --rule-light: #c9c9cc;
  }
  * { margin: 0; padding: 0; box-sizing: border-box; }
  html, body {
    width: 1093px; height: 1200px; overflow: hidden;
    background: var(--stage);
    font-family: "Raleway", sans-serif;
  }
  .card {
    position: absolute;
    width: 584px; height: 362px;
    border-radius: 18px;
    overflow: hidden;
  }
  .card-front { left: 265px; top: 224px; background: var(--card-grey); }
  .card-back  { left: 263px; top: 620px; background: var(--card-white); }

  /* company name block: plain square plus the name in one style */
  .brand {
    position: absolute;
    display: flex; flex-direction: column; align-items: center;
    text-align: center;
  }
  .brand-square { width: 54px; height: 54px; background: var(--brand-blue); margin-bottom: 16px; }
  .brand-name {
    font-family: "Raleway", sans-serif;
    font-weight: 400;
    font-size: 22px;
    line-height: 28px;
    color: var(--brand-blue);
  }
  .card-front .brand { left: 0; right: 0; top: 46px; }
  .card-front .brand-name { width: 300px; }
  .card-back .brand { left: 48px; width: 220px; top: 118px; }

  /* services */
  .services-title {
    position: absolute; left: 0; right: 0; top: 220px;
    text-align: center; color: var(--text-light);
    font-size: 19px; font-weight: 400;
  }
  .services-rule {
    position: absolute; left: 219px; width: 136px; top: 249px;
    height: 1px; background: var(--rule-light);
  }
  .services-band {
    position: absolute; left: 0; right: 0; top: 265px; height: 75px;
    background: var(--brand-blue);
    display: flex; flex-direction: column; justify-content: center; align-items: center;
    gap: 6px;
  }
  .services-line { display: flex; gap: 8px; color: var(--text-light); font-size: 13.4px; white-space: nowrap; line-height: 1.15; }
  .services-line li { list-style: none; display: flex; align-items: center; }
  .services-line li::before {
    content: ""; width: 6px; height: 6px; border-radius: 50%;
    background: var(--text-light); margin-right: 4px;
  }

  /* contact */
  .divider { position: absolute; left: 284px; top: 105px; width: 1.5px; height: 174px; background: var(--brand-blue); }
  .contact { position: absolute; left: 298px; top: 105px; font-family: "Montserrat", sans-serif; color: var(--text-dark); }
  .owners { color: var(--brand-blue); font-size: 21px; font-weight: 400; line-height: 1; margin-top: 3px; }
  .role { font-size: 12.5px; margin-top: 7px; line-height: 15px; }
  .address { font-family: "Raleway", sans-serif; font-size: 13.5px; font-weight: 500; line-height: 16px; margin-top: 10px; }
  .details { list-style: none; margin-top: 12px; }
  .details li { display: flex; align-items: center; font-size: 13px; height: 23px; }
  .details svg { width: 15px; height: 15px; margin-right: 9px; fill: var(--brand-blue); flex: none; }
</style>
</head>
<body>

<section class="card card-front">
  <div class="brand">
    <div class="brand-square"></div>
    <div class="brand-name">Halvorsen's Construction L.L.C</div>
  </div>
  <h2 class="services-title">OUR SERVICES</h2>
  <div class="services-rule"></div>
  <div class="services-band">
    <ul class="services-line">
      <li>Disaster Recovery</li>
      <li>Storm Damage Restoration</li>
      <li>Proactive Disaster Plan Management</li>
    </ul>
    <ul class="services-line">
      <li>Roof Repair/Restoration Structural Repair and Reconstruction</li>
      <li>Perimeter Fencing</li>
    </ul>
    <ul class="services-line">
      <li>Emergency Boarding and Tarping Service</li>
      <li>Emergency Tree Removal</li>
    </ul>
  </div>
</section>

<section class="card card-back">
  <div class="brand">
    <div class="brand-square"></div>
    <div class="brand-name">Halvorsen's Construction L.L.C</div>
  </div>
  <div class="divider"></div>
  <div class="contact">
    <h1 class="owners">Milo &amp; Trent Halvorsen</h1>
    <p class="role">owner operators<br>licensed and insured</p>
    <p class="address">48 Cedar Bluff Road<br>Brandon, MS 39042</p>
    <ul class="details">
      <li>
        <svg viewBox="0 0 16 16" aria-hidden="true"><path d="M1 6c0-2 3-3 7-3s7 1 7 3v1.5h-3.5V6H4.5v1.5H1z"/><path d="M4 8h8l1.5 6h-11z"/><circle cx="8" cy="11" r="1.6" fill="#fff"/></svg>
        5083716254
      </li>
      <li>
        <svg viewBox="0 0 16 16" aria-hidden="true"><path d="M1 3h14v10H1z"/><path d="M1.5 3.5 8 9l6.5-5.5" fill="none" stroke="#fff" stroke-width="1.3"/></svg>
        info@halvorsenbuild.com
      </li>
      <li>
        <svg viewBox="0 0 16 16" aria-hidden="true"><circle cx="8" cy="8" r="7"/><path d="M5 3.5c1.5 1 1 2.5 2.5 3s1 2-1 2.5-1 3 0 4M10.5 3c-.5 1.5.5 2 1.5 2.5M11 10c1 .5 1.5 1.5 1 2.5" fill="none" stroke="#fff" stroke-width="1.1"/></svg>
        www.halvorsenbuild.com
      </li>
    </ul>
  </div>
</section>

</body>
</html>
```